Caldrift - Where every box finds its place!

Hello,
I'd like to update, re-vamp, and re-tool this current power point presentation with slightly more professional appearance as well as more accurately reflect the website -caldrift.com- color scheme and sleek design scheme. Please see attached.
We at Caldrift pride ourselves on seeking to rework an archaic business into something progressive, cost effective, more reliable, and easily accessible in todays fast growing market that has only gotten more expensive, more costly and less indirect over the last couple years.

Target Market(s)

New updated and hassle free moving opportunities no matter how large or how small in a market that begs for a change

Industry/Entity Type

Logistics/Moving

Requirements
Must have
• The current color scheme from the -caldrift.com- website as well as the inclusion of the current data on the sample power point presentation provided but with updated graphics

```html
<!DOCTYPE html>
<html lang="en">
<head>
<meta charset="utf-8">
<title>Caldrift – Company Presentation</title>
<link href="https://fonts.googleapis.com/css2?family=Poppins:wght@400;500;600;700;800&display=swap" rel="stylesheet">
<style>
  :root{
    --blue:#0b4597;
    --blue-dark:#083679;
    --yellow:#fccf00;
    --stripe:#d9bd33;
    --white:#ffffff;
    --photo-warm-a:#c9a584;
    --photo-warm-b:#8d6a52;
    --photo-light-a:#e9e3dc;
    --photo-light-b:#b9a08a;
  }
  *{margin:0;padding:0;box-sizing:border-box}
  html,body{width:1200px;height:4068px;overflow:hidden;background:var(--white)}
  body{position:relative;font-family:'Poppins',sans-serif;color:var(--white)}
  .backdrop{position:absolute;inset:0;width:1200px;height:4068px}
  .slide{position:absolute;left:92px;width:1016px;height:572px;background:var(--blue);overflow:hidden}
  .slide>svg.shapes{position:absolute;inset:0;width:1016px;height:572px}
  .abs{position:absolute}
  .brand-title{font-weight:700;font-size:76px;line-height:1;letter-spacing:0.5px}
  .brand-word{font-weight:700;color:var(--yellow);line-height:1}
  .tagline{font-weight:400;font-size:36px;line-height:1}
  .url{font-size:11px;font-weight:400}
  .slide-title{font-weight:800;font-size:54px;line-height:1.2}
  .about-copy{font-size:12.5px;line-height:33px;width:450px}
  .about-copy p+p{margin-top:33px}
  .card{position:absolute;top:234px;width:232px;height:169px;background:var(--white);border-radius:8px;color:var(--blue-dark);text-align:center}
  .card svg{display:block;margin:18px auto 0;width:52px;height:52px}
  .card h3{font-size:20px;font-weight:700;margin-top:6px;line-height:1.2}
  .card p{font-size:12px;font-weight:600;line-height:18px;margin:4px 18px 0}
  .card-desc{position:absolute;top:422px;width:232px;text-align:center;font-size:12.5px;line-height:18.5px;padding:0 10px}
  .step-num{position:absolute;width:48px;height:48px;border:2.5px solid var(--white);border-radius:50%;background:var(--blue);font-size:30px;font-weight:400;display:flex;align-items:center;justify-content:center;line-height:1}
  .step-label{position:absolute;width:237px;text-align:center;color:var(--blue-dark);font-weight:700;font-size:21px;line-height:1}
  .step-desc{position:absolute;width:237px;text-align:center;font-size:12.5px;line-height:17.5px;padding:0 18px}
  .contact{font-size:13px;line-height:22px}
  .contact-icon{position:absolute;width:18px;height:18px}
  .thanks{font-weight:800;font-size:57px;line-height:63px;color:var(--blue-dark)}
</style>
</head>
<body>

<svg class="backdrop" viewBox="0 0 1200 4068" aria-hidden="true">
  <polygon fill="var(--stripe)" points="500,0 640,0 0,860 0,600"/>
  <polygon fill="var(--stripe)" points="1200,400 1200,720 540,1700 360,1700"/>
  <polygon fill="var(--stripe)" points="0,1250 0,1700 420,1250 300,1250"/>
  <polygon fill="var(--stripe)" points="780,1300 1000,1300 300,2400 80,2400"/>
  <polygon fill="var(--stripe)" points="1200,2000 1200,2400 700,3000 500,3000"/>
  <polygon fill="var(--stripe)" points="0,2500 0,2900 560,2620 450,2620"/>
  <polygon fill="var(--stripe)" points="1200,3100 1200,3500 850,3900 600,3900"/>
  <polygon fill="var(--stripe)" points="520,3950 720,3950 560,4068 360,4068"/>
</svg>

<!-- Cover -->
<section class="slide" style="top:106px">
  <svg class="shapes" viewBox="0 0 1016 572">
    <polygon fill="var(--yellow)" points="430,572 1016,572 1016,115 860,115"/>
    <g role="img" aria-label="Photo of a smiling person carrying a moving box">
      <defs><linearGradient id="cg1" x1="0" y1="0" x2="1" y2="1"><stop offset="0" stop-color="var(--photo-warm-a)"/><stop offset="1" stop-color="var(--photo-warm-b)"/></linearGradient></defs>
      <polygon fill="url(#cg1)" points="640,80 720,0 1016,0 1016,115 860,115 770,250"/>
      <polygon fill="url(#cg1)" points="280,300 520,300 720,572 520,572"/>
    </g>
    <polygon fill="var(--blue)" points="640,190 700,150 880,330 820,370"/>
  </svg>
  <div class="abs brand-title" style="left:56px;top:108px">Caldrift</div>
  <div class="abs tagline" style="left:56px;top:222px">Moving for the next generation</div>
  <div class="abs url" style="left:58px;top:540px">www.caldrift.com</div>
</section>

<!-- About -->
<section class="slide" style="top:766px">
  <svg class="shapes" viewBox="0 0 1016 572">
    <polygon fill="var(--yellow)" points="428,572 1016,572 1016,118 900,118 900,470 560,470"/>
    <rect x="504" y="54" width="407" height="453" rx="10" fill="var(--photo-light-b)" role="img" aria-label="Photo of a couple giving a high five among moving boxes"/>
  </svg>
  <h1 class="abs slide-title" style="left:58px;top:28px">About Us</h1>
  <div class="abs about-copy" style="left:58px;top:126px">
    <p>Caldrift is the next logical evolution in professional moving. Professional moving clients have battled soaring prices, acute capacity problems and deteriorating service levels.</p>
    <p>Caldrift was founded by lifelong moving professionals who have developed the answer to better moving services. Poised as THE industry disruptor, we deliver faster, offer guaranteed prices and even offer no credit check financing options. We are a technology first organization using proprietary software to deliver moving's best service experience.</p>
  </div>
</section>

<!-- Vision / Mission / Goal -->
<section class="slide" style="top:1424px">
  <svg class="shapes" viewBox="0 0 1016 572">
    <rect x="0" y="46" width="1016" height="290" fill="var(--photo-light-a)" role="img" aria-label="Photo of a happy family with two children at home"/>
  </svg>
  <div class="abs brand-word" style="left:0;width:1016px;text-align:center;top:10px;font-size:28px">Caldrift</div>

  <div class="card" style="left:58px">
    <svg viewBox="0 0 52 52" fill="none" stroke="var(--blue-dark)" stroke-width="1.8"><path d="M4 30 Q26 10 48 30 Q26 50 4 30Z"/><circle cx="26" cy="30" r="8"/><path d="M22 33v-3M26 33v-5M30 33v-7"/><path d="M26 4v10M22 8l4-4 4 4"/></svg>
    <h3>Our Vision</h3>
    <p>Revolutionize an $86B industry by providing great value to everyone involved</p>
  </div>
  <div class="card" style="left:390px">
    <svg viewBox="0 0 52 52" fill="none" stroke="var(--blue-dark)" stroke-width="1.8"><circle cx="24" cy="28" r="18"/><circle cx="24" cy="28" r="11"/><circle cx="24" cy="28" r="4"/><path d="M24 28L44 10M38 10h6v6"/></svg>
    <h3>Our Mission</h3>
    <p>Disrupt a sleepy giant of an inefficient industry</p>
  </div>
  <div class="card" style="left:723px">
    <svg viewBox="0 0 52 52" fill="none" stroke="var(--blue-dark)" stroke-width="1.8"><path d="M6 46h40M10 46V38h10v-8h10v-8h10v24"/><path d="M34 22V4l10 4-10 4"/></svg>
    <h3>Our Goal</h3>
    <p>Becoming the moving platform of choice</p>
  </div>

  <div class="card-desc" style="left:58px">Caldrift Customers - Consumers, Movers, Corporate Clients, and Relocation Management Companies all receive better value with</div>
  <div class="card-desc" style="left:390px">Caldrift's deep understanding of the professional moving industry, supported by extensive market research has set Caldrift up for ultimate success in disrupting this industry by creating cost-saving efficiencies throughout.</div>
  <div class="card-desc" style="left:723px">As Caldrift's market share grows, the customer acquisition cost and operational cost plummets. This creates even more market penetration, more efficiencies, and exponential growth.</div>
</section>

<!-- Industry problems -->
<section class="slide" style="top:2078px">
  <svg class="shapes" viewBox="0 0 1016 572" fill="none">
    <polygon fill="var(--yellow)" points="177,114 296,216 58,216"/>
    <polygon fill="var(--yellow)" points="398,250 516,353 279,353"/>
    <polygon fill="var(--yellow)" points="617,114 736,216 497,216"/>
    <polygon fill="var(--yellow)" points="835,250 957,353 717,353"/>
    <g stroke="var(--white)" stroke-width="3" stroke-linecap="round">
      <path d="M228,74 Q350,70 378,178"/><path d="M368,168 378,180 386,166"/>
      <path d="M420,178 Q450,90 562,76"/><path d="M550,68 564,76 552,86"/>
      <path d="M670,74 Q790,70 818,178"/><path d="M808,168 818,180 826,166"/>
    </g>
    <g stroke="var(--white)" stroke-width="1.8">
      <path d="M170,146 h14 M172,146 q-12 10 -8 24 h26 q4 -14 -8 -24"/><text x="177" y="166" fill="var(--white)" stroke="none" font-size="11" text-anchor="middle" font-family="Poppins,sans-serif">$</text>
      <circle cx="398" cy="298" r="9"/><circle cx="398" cy="298" r="15" stroke-dasharray="5 3"/>
      <path d="M605,160 l12 -14 12 14 -12 14z M605,160 v10 l12 12 12 -12 v-10"/>
      <circle cx="831" cy="293" r="9"/><path d="M838,300 l10 10"/>
    </g>
  </svg>
  <div class="step-num" style="left:153px;top:52px">01</div>
  <div class="step-num" style="left:374px;top:188px">02</div>
  <div class="step-num" style="left:593px;top:52px">03</div>
  <div class="step-num" style="left:811px;top:188px">04</div>

  <div class="step-label" style="left:58px;top:187px">Cost</div>
  <div class="step-label" style="left:279px;top:323px">Capacity</div>
  <div class="step-label" style="left:498px;top:187px">Service</div>
  <div class="step-label" style="left:719px;top:323px">Transparancy</div>

  <div class="step-desc" style="left:58px;top:232px">Moving cost has skyrocketed over the last three years. Charges have increased 38% since 2018.</div>
  <div class="step-desc" style="left:279px;top:368px">Long-haul driver shortages and limited equipment coupled with growing demand has pushed capacity to a crisis state</div>
  <div class="step-desc" style="left:498px;top:232px">Quality labor has been difficult to source and afford. Virtually all RMC's report a decline in service quality</div>
  <div class="step-desc" style="left:719px;top:368px">Too many margin layers...van line, agent, driver and help. In addition, charges are convoluted and confusing</div>
</section>

<!-- Questions -->
<section class="slide" style="top:2733px">
  <svg class="shapes" viewBox="0 0 1016 572">
    <polygon fill="var(--white)" points="520,572 1016,572 1016,60 973,60 973,401 660,401"/>
    <rect x="568" y="36" width="405" height="365" rx="10" fill="var(--yellow)"/>
    <rect x="556" y="47" width="406" height="341" rx="8" fill="var(--photo-light-b)" role="img" aria-label="Photo of an excited woman opening a moving box"/>
    <rect x="698" y="394" width="213" height="162" rx="20" fill="#dfe7f3" role="img" aria-label="Illustration of question marks"/>
  </svg>
  <div class="abs brand-word" style="left:56px;top:26px;font-size:36px">Caldrift</div>
  <h2 class="abs slide-title" style="left:56px;top:180px;line-height:66px">Do you have<br>any questions?</h2>
</section>

<!-- Thank you -->
<section class="slide" style="top:3388px">
  <svg class="shapes" viewBox="0 0 1016 572">
    <defs><linearGradient id="cg2" x1="0" y1="0" x2="1" y2="1"><stop offset="0" stop-color="var(--photo-light-a)"/><stop offset="1" stop-color="var(--photo-warm-b)"/></linearGradient></defs>
    <polygon fill="var(--yellow)" points="700,572 1016,572 1016,140 900,140 820,300"/>
    <g role="img" aria-label="Photo of movers carrying boxes into a new home">
      <polygon fill="url(#cg2)" points="640,0 1016,0 1016,140 900,140 860,260"/>
      <polygon fill="url(#cg2)" points="262,340 520,300 760,572 530,572"/>
    </g>
    <polygon fill="var(--blue)" points="580,0 650,0 880,240 830,280"/>
  </svg>
  <div class="abs brand-title" style="left:56px;top:104px">Caldrift</div>

  <svg class="contact-icon" style="left:56px;top:250px" viewBox="0 0 18 18" fill="none" stroke="var(--white)" stroke-width="1.4"><path d="M9 17s6-6 6-10A6 6 0 0 0 3 7c0 4 6 10 6 10z"/><circle cx="9" cy="7" r="2"/></svg>
  <div class="abs contact" style="left:84px;top:245px">48 Harbor Lane<br>Brookfield, OK 73010</div>

  <svg class="contact-icon" style="left:56px;top:331px" viewBox="0 0 18 18" fill="none" stroke="var(--white)" stroke-width="1.4"><path d="M4 2l3 3-2 2c1 3 3 5 6 6l2-2 3 3-2 3C7 17 1 11 1 4z"/></svg>
  <div class="abs contact" style="left:84px;top:329px">(800) 555-0142</div>

  <svg class="contact-icon" style="left:56px;top:392px" viewBox="0 0 18 18" fill="none" stroke="var(--white)" stroke-width="1.4"><circle cx="9" cy="9" r="7.5"/><path d="M1.5 9h15M9 1.5c3 3 3 12 0 15M9 1.5c-3 3-3 12 0 15"/></svg>
  <div class="abs contact" style="left:84px;top:389px">caldrift.com<br>support@caldrift.com</div>

  <div class="abs thanks" style="left:797px;top:350px">Thank<br>You!</div>
  <div class="abs url" style="left:58px;top:540px">www.caldrift.com</div>
</section>

</body>
</html>
```